Looking for a modern, Professional business card design

We have a simple business card, but are looking for a more modern, professional look. A sample of the basic card is attached as well as the logo. We would also like to add that we offer:
Struggling with your finances?
- Learn to become debt free
- Discover the power of cash
- Control your money instead of it controlling you
Let us help you achieve a new level of financial freedom!
Also, we would like to have a "SPECIAL OFFER!: FREE 30 minute consultation"
Financial Planning

```html
<!DOCTYPE html>
<html lang="en">
<head>
<meta charset="UTF-8">
<title>Brightway Money Coaching – Business Card</title>
<link href="https://fonts.googleapis.com/css2?family=Open+Sans:ital,wght@0,400;0,600;0,700;1,400&display=swap" rel="stylesheet">
<style>
  :root {
    --backdrop: #e9e6e1;
    --lime: #9bcb3b;
    --lime-light: #8cc63f;
    --green-dark: #2aa14a;
    --green-text: #2e9e46;
    --ink: #1d1d1b;
    --ink-soft: #333333;
    --paper: #ffffff;
  }
  * { margin: 0; padding: 0; box-sizing: border-box; }
  html, body { width: 1200px; height: 900px; overflow: hidden; }
  body {
    background: var(--backdrop);
    font-family: "Open Sans", Arial, sans-serif;
    color: var(--ink);
    position: relative;
  }
  .card {
    position: absolute;
    width: 600px;
    height: 343px;
    box-shadow: 0 4px 14px rgba(0,0,0,.18);
    overflow: hidden;
  }
  /* back side */
  .card-back {
    left: 300px; top: 72px;
    background: var(--lime);
    text-align: center;
  }
  .brand {
    display: flex; align-items: center; justify-content: center; gap: 10px;
  }
  .brand-dot {
    width: 22px; height: 22px; border-radius: 50%;
    background: var(--green-dark);
  }
  .brand-name {
    font-weight: 700; color: var(--ink); letter-spacing: .5px;
  }
  .card-back .brand { margin-top: 38px; }
  .card-back .brand-name { font-size: 30px; }
  .tagline { font-size: 11px; color: var(--ink-soft); margin-top: 2px; }
  .pitch-heading { font-weight: 700; font-size: 17px; margin-top: 22px; }
  .pitch-list { list-style: none; font-size: 15px; line-height: 20px; margin-top: 4px; }
  .pitch-close { font-size: 13px; font-style: italic; margin-top: 6px; }
  .offer { font-weight: 700; font-size: 19px; margin-top: 14px; letter-spacing: .3px; }

  /* front side */
  .card-front {
    left: 300px; top: 485px;
    background: var(--paper);
  }
  .card-front .bands { position: absolute; inset: 0; }
  .person { position: absolute; left: 66px; top: 30px; }
  .person-name { color: var(--green-text); font-weight: 700; font-size: 19px; }
  .person-role { font-size: 14px; color: var(--ink-soft); }
  .card-front .brand {
    position: absolute; left: 300px; top: 160px; justify-content: flex-start;
  }
  .card-front .brand-name { font-size: 26px; }
  .card-front .tagline { position: absolute; left: 332px; top: 200px; }
  .contact { position: absolute; left: 30px; top: 170px; list-style: none; font-size: 15px; color: var(--ink); }
  .contact li { display: flex; align-items: center; gap: 10px; line-height: 22px; }
  .contact svg { width: 12px; height: 12px; flex: none; }
</style>
</head>
<body>

<section class="card card-back" aria-label="Card back">
  <div class="brand">
    <span class="brand-dot"></span>
    <span class="brand-name">BRIGHTWAY MONEY COACHING</span>
  </div>
  <p class="tagline">Achieve a new level of personal freedom</p>
  <h2 class="pitch-heading">STRUGGLING WITH YOUR FINANCES?</h2>
  <ul class="pitch-list">
    <li>Learn to become debt free</li>
    <li>Discover the power of cash</li>
    <li>Control your money instead of it controlling you</li>
  </ul>
  <p class="pitch-close">Let us help you achieve a new level of financial freedom!</p>
  <p class="offer">SPECIAL OFFER!: FREE 30 MINUTE CONSULTATION</p>
</section>

<section class="card card-front" aria-label="Card front">
  <svg class="bands" viewBox="0 0 600 343" width="600" height="343" aria-hidden="true">
    <polygon points="0,40 50,40 30,70 0,70" fill="var(--lime-light)"/>
    <polygon points="0,258 600,258 600,268 190,268 175,300 0,300" fill="var(--lime-light)"/>
    <polygon points="200,280 600,280 600,343 170,343" fill="var(--green-dark)"/>
  </svg>

  <div class="person">
    <h1 class="person-name">Daniel R. Carver</h1>
    <p class="person-role">Personal financial coach</p>
  </div>

  <ul class="contact">
    <li><svg viewBox="0 0 12 12"><path d="M2 1l2 0 1 3-1.5 1a7 7 0 0 0 3.5 3.5L8 7l3 1v2a1 1 0 0 1-1 1A9 9 0 0 1 1 2a1 1 0 0 1 1-1z" fill="var(--green-dark)"/></svg>(555) 014-2290</li>
    <li><svg viewBox="0 0 12 12"><rect x="0.5" y="2" width="11" height="8" fill="var(--green-dark)"/><path d="M1 2.5l5 4 5-4" stroke="#fff" fill="none"/></svg>daniel@brightwaymoney.com</li>
    <li><svg viewBox="0 0 12 12"><circle cx="6" cy="6" r="5.5" fill="var(--green-dark)"/><path d="M1 6h10M6 .5c-2.5 3-2.5 8 0 11M6 .5c2.5 3 2.5 8 0 11" stroke="#fff" stroke-width=".8" fill="none"/></svg>www.brightwaymoney.com</li>
  </ul>

  <div class="brand">
    <span class="brand-dot"></span>
    <span class="brand-name">BRIGHTWAY</span>
  </div>
  <p class="tagline">Achieve a new level of personal freedom</p>
</section>

</body>
</html>
```